Social Media App Needs PPT Template

We need a PowerPoint template for a new social media company based in the DC area called "Bold Ledger." We provide an interactive digital platform for executives to share actionable advice. We would like to see designs that use our orange logo color as an accent, but are mainly grey, white, and black. The final design should communicate clean, chic, modern, and professional.

Target Market(s)

Executives

Industry/Entity Type

Information Technology

Font styles to use
Sans Serif

Colors
f78f20
fbe7d2
ffffff
000000
e8e8e8
757575

Requirements
Must have
• My project must have title page and many options for the body of the ppt (graphs, tables, etc). It also needs to be easy to modify. I must have someone who is experienced in creating powerpoint templates.
Nice to have
• It would be nice to have a very modern and clean design that includes the logo on every page, but still leaves a lot of room for the content of the slide
Should not have
• My design project should not look to busy.

```html
<!DOCTYPE html>
<html lang="en">
<head>
<meta charset="utf-8">
<title>Bold Ledger — Presentation Template</title>
<link href="https://fonts.googleapis.com/css2?family=Lato:wght@300;400;700;900&display=swap" rel="stylesheet">
<style>
:root{
  --orange:#f78f20;
  --pale-orange:#fbe7d2;
  --navy:#252b37;
  --ink:#231f20;
  --grey:#757575;
  --mid-grey:#6d6d6d;
  --soft-grey:#cfcfcf;
  --light:#e8e8e8;
  --white:#ffffff;
  --board:#c9c9c9;
  --text:#5a5a5a;
}
*{box-sizing:border-box;margin:0;padding:0}
html,body{width:1200px;height:2400px;overflow:hidden;background:var(--board);font-family:'Lato',Arial,sans-serif}
.sheet{display:grid;grid-template-columns:600px 600px;grid-template-rows:repeat(5,480px);width:1200px;height:2400px}
.cell{position:relative;border-right:1px solid #d6d6d6;border-bottom:1px solid #d6d6d6}
.page-label{position:absolute;top:24px;left:0;width:100%;text-align:center;color:#f1f1f1;font-size:15px}
.slide{position:absolute;left:59px;top:72px;width:482px;height:360px;background:var(--white);overflow:hidden}
.sidebar{position:absolute;left:0;top:0;bottom:0;width:86px;background:var(--navy)}
.brand{position:absolute;top:18px;left:0;width:86px;text-align:center}
.brand-dot{display:block;width:12px;height:12px;border-radius:50%;background:var(--orange);margin:0 auto 5px}
.brand-name{color:var(--white);font-weight:700;font-size:10px;letter-spacing:.5px;line-height:1.1}
.site{position:absolute;left:9px;bottom:10px;color:#a9afbb;font-size:7.5px}
.title{position:absolute;left:101px;top:48px;color:var(--orange);font-size:19px;font-weight:400}
.title-rule{position:absolute;left:101px;top:77px;width:361px;height:1px;background:#f6cfa5}
.folio{position:absolute;right:20px;bottom:9px;width:62px;border-top:1px solid #cfcfcf;padding-top:4px;text-align:right;color:#9a9a9a;font-size:6px}
.body-text{color:var(--text);font-size:6.4px;line-height:1.4}
.justify{text-align:justify}
.abs{position:absolute}

/* cover */
.cover{background:var(--navy)}
.cover-photo{position:absolute;left:0;top:0}
.cover-brand{position:absolute;left:330px;top:170px;width:150px;text-align:center}
.cover-brand .brand-dot{width:20px;height:20px;margin-bottom:8px}
.cover-brand .brand-name{font-size:22px}
.cover-rule{position:absolute;left:85px;top:282px;width:378px;height:1px;background:var(--orange)}
.tagline{position:absolute;left:101px;top:291px;color:#d3d7de;font-size:14.5px;font-weight:300}
.cover-rule-thin{position:absolute;left:101px;top:316px;width:362px;height:1px;background:#4a5263}
.cover-site{position:absolute;right:20px;bottom:18px;color:#a9afbb;font-size:8px}

/* about */
.about-lead{font-weight:700;color:#333;margin-bottom:6px}
.photo{background:linear-gradient(135deg,#3c4250,#1a1e27 60%,#505766)}

/* features */
.feature{position:absolute;top:128px;width:112px;text-align:center}
.feature svg{display:block;margin:0 auto 14px}

/* legend */
.legend{position:absolute;left:428px;top:102px;font-size:6px;color:#666;line-height:1.6}
.legend i{display:inline-block;width:5px;height:5px;margin-right:3px;vertical-align:middle}

/* donut */
.segment-label{position:absolute;width:120px}
.segment-head{font-size:8.5px;font-weight:700;color:var(--navy);margin-bottom:4px;padding-bottom:2px}
.segment-head.accent{color:var(--orange)}
.segment-head.muted{color:#9a9a9a;font-weight:400}
.segment-label .body-text{color:#8a8a8a}

/* table */
.data-table{position:absolute;left:101px;top:122px;width:361px;border-collapse:collapse;font-size:9.5px;color:var(--grey)}
.data-table th{font-weight:400;font-size:7px;height:28px;border-top:1px solid #cfcfcf;color:#777}
.data-table td{height:30px;text-align:center}
.data-table td.row-name{text-align:left;padding-left:43px;font-size:7.5px}
.data-table tr.band td{background:var(--orange);color:var(--white)}
.data-table tr.gap td{height:5px;padding:0}

/* team */
.member{position:absolute;width:190px}
.member-photo{position:absolute;left:0;top:0;width:59px;height:59px;background:linear-gradient(160deg,#b9b4ad,#6b6660)}
.member-info{position:absolute;left:66px;top:6px;width:116px}
.member-name{font-size:9px;font-weight:700;color:var(--navy)}
.member-role{font-size:6.5px;color:#999;margin:2px 0 6px}

/* stats */
.stat{position:absolute;width:166px;height:75px;color:var(--white)}
.stat svg{position:absolute;left:12px;top:22px}
.stat-figure{position:absolute;left:60px;top:12px;font-size:13px;font-weight:400}
.stat-note{position:absolute;left:60px;top:30px;width:100px;font-size:5.8px;line-height:1.35}
.stat.orange{background:var(--orange)}
.stat.grey{background:var(--mid-grey)}
.stat.navy{background:var(--navy)}
.stat.ink{background:var(--ink)}

/* closing */
.closing-band{position:absolute;left:0;top:0;width:482px;height:267px;background:var(--navy)}
.closing-brand{position:absolute;left:0;top:62px;width:482px;text-align:center}
.closing-brand .brand-dot{width:16px;height:16px}
.closing-brand .brand-name{font-size:16px}
.thanks{position:absolute;left:0;top:190px;width:482px;text-align:center;color:var(--white);font-size:44px;font-weight:300;letter-spacing:1px}
.closing-site{position:absolute;left:0;top:326px;width:482px;text-align:center;color:#777;font-size:9px}
</style>
</head>
<body>
<main class="sheet">

  <!-- 1 cover -->
  <section class="cell">
    <div class="page-label">Page 1</div>
    <div class="slide cover">
      <svg class="cover-photo" width="482" height="290" viewBox="0 0 482 290">
        <defs>
          <linearGradient id="photoTone" x1="0" y1="0" x2="1" y2="1">
            <stop offset="0" stop-color="#7f95ad"/>
            <stop offset=".45" stop-color="#3b4658"/>
            <stop offset="1" stop-color="#1c2029"/>
          </linearGradient>
        </defs>
        <path role="img" aria-label="Photo of a hand typing on a laptop keyboard with a rising growth graphic" d="M0 0 H482 V20 Q260 170 0 285 Z" fill="url(#photoTone)"/>
      </svg>
      <div class="cover-brand"><span class="brand-dot"></span><div class="brand-name">Bold Ledger</div></div>
      <div class="cover-rule"></div>
      <div class="tagline">interactive digital platform to share actionable advice</div>
      <div class="cover-rule-thin"></div>
      <div class="cover-site">www.boldledger.com</div>
    </div>
  </section>

  <!-- 2 about -->
  <section class="cell">
    <div class="page-label">Page 2</div>
    <div class="slide">
      <div class="sidebar"><div class="brand"><span class="brand-dot"></span><div class="brand-name">Bold Ledger</div></div><div class="site">boldledger.com</div></div>
      <h1 class="title">About Our Company</h1>
      <div class="title-rule"></div>
      <div class="abs body-text justify" style="left:101px;top:98px;width:180px">
        <p class="about-lead">Bold Ledger connects executives through a focused digital space where proven leaders exchange clear, practical advice on strategy, growth, teams and the daily decisions that shape a business. Our members come from every sector and share one goal: better choices, made faster, with less noise.</p>
        <p>Members publish short insights, ask direct questions and respond with real experience. Every contribution is reviewed for relevance, so the feed stays useful, calm and easy to scan. Discussion groups form around industries and roles, letting leaders find peers who face the same pressures and compare what actually worked for them. Weekly digests gather the strongest threads, and private circles let small groups work through a single challenge together. Profiles highlight expertise rather than follower counts, so advice is judged on its merit. Members can save posts, follow topics and invite trusted colleagues, building a network that grows in quality over time and keeps every conversation grounded in practical results.</p>
      </div>
      <div class="abs body-text justify" style="left:293px;top:98px;width:170px">
        <p>The platform is built for busy schedules. Short formats, clear summaries and trusted voices help every member act on advice the same day they read it. Mobile and desktop access keep the network close at hand, whether between meetings or on the road, and quiet notifications respect focused work time.</p>
      </div>
      <div class="abs photo" role="img" aria-label="Photo of an executive in a suit holding a tablet with glowing network icons" style="left:293px;top:188px;width:170px;height:100px"></div>
      <div class="folio">Page 1</div>
    </div>
  </section>

  <!-- 3 features -->
  <section class="cell">
    <div class="page-label">Page 3</div>
    <div class="slide">
      <div class="sidebar"><div class="brand"><span class="brand-dot"></span><div class="brand-name">Bold Ledger</div></div><div class="site">boldledger.com</div></div>
      <h1 class="title">Title of the page</h1>
      <div class="title-rule"></div>
      <div class="feature" style="left:102px">
        <svg width="40" height="30" viewBox="0 0 40 30" fill="none" stroke="var(--navy)" stroke-width="2"><rect x="6" y="3" width="28" height="19"/><rect x="10" y="7" width="20" height="11"/><path d="M1 26 H39 L36 22 H4 Z"/></svg>
        <p class="body-text">Add a short description of this point here. Keep the wording brief so the slide stays open and easy to read at a glance. Use one clear idea per column and support it with a simple fact or example that your audience will remember after the meeting ends.</p>
      </div>
      <div class="feature" style="left:230px">
        <svg width="40" height="30" viewBox="0 0 40 30" fill="none" stroke="var(--orange)" stroke-width="2" stroke-linejoin="round"><path d="M2 8 L9 5 L15 17 L9 20 Z"/><path d="M38 8 L31 5 L25 17 L31 20 Z"/><path d="M12 18 L18 24 Q20 26 22 24 L28 18"/><path d="M14 9 L20 7 L25 10 L20 14 Q18 15 17 13"/><path d="M16 21 L19 18 M19 23 L22 20"/></svg>
        <p class="body-text">Add a short description of this point here. Keep the wording brief so the slide stays open and easy to read at a glance. Use one clear idea per column and support it with a simple fact or example that your audience will remember after the meeting ends.</p>
      </div>
      <div class="feature" style="left:356px">
        <svg width="40" height="30" viewBox="0 0 40 30" fill="none" stroke="var(--navy)" stroke-width="2" stroke-linejoin="round"><rect x="8" y="13" width="6" height="14"/><path d="M14 14 L20 6 Q21 2 24 4 Q25 7 23 12 H31 Q34 13 32 16 Q34 18 31 20 Q33 22 30 24 Q31 27 27 27 H14"/></svg>
        <p class="body-text">Add a short description of this point here. Keep the wording brief so the slide stays open and easy to read at a glance. Use one clear idea per column and support it with a simple fact or example that your audience will remember after the meeting ends.</p>
      </div>
      <div class="folio">Page 2</div>
    </div>
  </section>

  <!-- 4 bar chart -->
  <section class="cell">
    <div class="page-label">Page 4</div>
    <div class="slide">
      <div class="sidebar"><div class="brand"><span class="brand-dot"></span><div class="brand-name">Bold Ledger</div></div><div class="site">boldledger.com</div></div>
      <h1 class="title">Title of the page</h1>
      <div class="title-rule"></div>
      <svg class="abs" style="left:101px;top:100px" width="320" height="120" viewBox="0 0 320 120" font-family="Lato, sans-serif" font-size="6" fill="#777">
        <g stroke="#e2e2e2" stroke-dasharray="2 2"><line x1="14" y1="5" x2="310" y2="5"/><line x1="14" y1="23" x2="310" y2="23"/><line x1="14" y1="41" x2="310" y2="41"/><line x1="14" y1="59" x2="310" y2="59"/><line x1="14" y1="77" x2="310" y2="77"/></g>
        <line x1="14" y1="95" x2="310" y2="95" stroke="#cfcfcf"/>
        <text x="4" y="7">5</text><text x="4" y="25">4</text><text x="4" y="43">3</text><text x="4" y="61">2</text><text x="4" y="79">1</text><text x="4" y="97">0</text>
        <rect x="46" y="17.6" width="14" height="77.4" fill="var(--orange)"/><rect x="60" y="32" width="14" height="63" fill="var(--navy)"/><rect x="74" y="23" width="14" height="72" fill="var(--mid-grey)"/>
        <rect x="141" y="28.4" width="14" height="66.6" fill="var(--orange)"/><rect x="155" y="15.8" width="14" height="79.2" fill="var(--navy)"/><rect x="169" y="32" width="14" height="63" fill="var(--mid-grey)"/>
        <rect x="236" y="39.2" width="14" height="55.8" fill="var(--orange)"/><rect x="250" y="21.2" width="14" height="73.8" fill="var(--navy)"/><rect x="264" y="14" width="14" height="81" fill="var(--mid-grey)"/>
        <text x="52" y="108">Category 1</text><text x="147" y="108">Category 2</text><text x="242" y="108">Category 3</text>
      </svg>
      <div class="legend"><div><i style="background:var(--orange)"></i>Series 1</div><div><i style="background:var(--navy)"></i>Series 2</div><div><i style="background:var(--mid-grey)"></i>Series 3</div></div>
      <p class="abs body-text" style="left:101px;top:240px;width:361px">Use this space to explain what the chart shows. Point out the key trend, note any change between categories and state the action it suggests for the team this quarter. Keep the note short and focused on the one result that matters most, then add the source of the figures and the date they were collected so the audience can trust the numbers and follow up later.</p>
      <div class="folio">Page 3</div>
    </div>
  </section>

  <!-- 5 area chart -->
  <section class="cell">
    <div class="page-label">Page 5</div>
    <div class="slide">
      <div class="sidebar"><div class="brand"><span class="brand-dot"></span><div class="brand-name">Bold Ledger</div></div><div class="site">boldledger.com</div></div>
      <h1 class="title">Title of the page</h1>
      <div class="title-rule"></div>
      <svg class="abs" style="left:101px;top:100px" width="320" height="120" viewBox="0 0 320 120" font-family="Lato, sans-serif" font-size="6" fill="#777">
        <g stroke="#e2e2e2" stroke-dasharray="2 2"><line x1="14" y1="5" x2="310" y2="5"/><line x1="14" y1="23" x2="310" y2="23"/><line x1="14" y1="41" x2="310" y2="41"/><line x1="14" y1="59" x2="310" y2="59"/><line x1="14" y1="77" x2="310" y2="77"/></g>
        <text x="4" y="7">5</text><text x="4" y="25">4</text><text x="4" y="43">3</text><text x="4" y="61">2</text><text x="4" y="79">1</text><text x="4" y="97">0</text>
        <polygon points="18,66 160,32 300,12 300,95 18,95" fill="var(--navy)"/>
        <polygon points="18,64 105,27 200,48 300,60 300,95 18,95" fill="var(--orange)"/>
        <polygon points="18,63 160,50 300,44 300,95 18,95" fill="#a9a9a9"/>
        <line x1="14" y1="95" x2="310" y2="95" stroke="#cfcfcf"/>
        <text x="18" y="108">Category 1</text><text x="146" y="108">Category 2</text><text x="275" y="108">Category 3</text>
      </svg>
      <div class="legend"><div><i style="background:var(--orange)"></i>Series 1</div><div><i style="background:var(--navy)"></i>Series 2</div><div><i style="background:#a9a9a9"></i>Series 3</div></div>
      <p class="abs body-text" style="left:101px;top:240px;width:361px">Use this space to explain what the chart shows. Point out the key trend, note any change between categories and state the action it suggests for the team this quarter. Keep the note short and focused on the one result that matters most, then add the source of the figures and the date they were collected so the audience can trust the numbers and follow up later.</p>
      <div class="folio">Page 4</div>
    </div>
  </section>

  <!-- 6 donut -->
  <section class="cell">
    <div class="page-label">Page 6</div>
    <div class="slide">
      <div class="sidebar"><div class="brand"><span class="brand-dot"></span><div class="brand-name">Bold Ledger</div></div><div class="site">boldledger.com</div></div>
      <h1 class="title">Title of the page</h1>
      <div class="title-rule"></div>
      <svg class="abs" style="left:0;top:0" width="482" height="360" viewBox="0 0 482 360" font-family="Lato, sans-serif">
        <g fill="none" stroke-width="39">
          <path d="M242 131.5 A39.5 39.5 0 0 1 281.5 171" stroke="var(--orange)"/>
          <path d="M281.5 171 A39.5 39.5 0 0 1 242 210.5" stroke="var(--soft-grey)"/>
          <path d="M242 210.5 A39.5 39.5 0 0 1 202.5 171" stroke="var(--navy)"/>
          <path d="M202.5 171 A39.5 39.5 0 0 1 242 131.5" stroke="var(--mid-grey)"/>
        </g>
        <g stroke="var(--white)" stroke-width="1.5"><line x1="242" y1="110" x2="242" y2="232"/><line x1="181" y1="171" x2="303" y2="171"/></g>
        <g fill="var(--white)" font-size="9" text-anchor="middle"><text x="262" y="157">25%</text><text x="262" y="193">25%</text><text x="222" y="193">25%</text><text x="222" y="157">25%</text></g>
        <g fill="none" stroke-width="1">
          <polyline points="104,117 200,117 214,132" stroke="var(--navy)"/>
          <polyline points="462,117 341,117 272,132" stroke="var(--orange)"/>
          <polyline points="104,238 200,238 214,212" stroke="var(--navy)"/>
          <polyline points="462,238 341,238 272,212" stroke="#bdbdbd"/>
        </g>
      </svg>
      <div class="segment-label" style="left:104px;top:104px"><div class="segment-head">NOBIS VIDENTUR</div><p class="body-text">Short note about this share of the total goes here, in a few words.</p></div>
      <div class="segment-label" style="left:341px;top:104px"><div class="segment-head accent">NOBIS VIDENTUR</div><p class="body-text">Short note about this share of the total goes here, in a few words.</p></div>
      <div class="segment-label" style="left:104px;top:225px"><div class="segment-head">NOBIS VIDENTUR</div><p class="body-text">Short note about this share of the total goes here, in a few words.</p></div>
      <div class="segment-label" style="left:341px;top:225px"><div class="segment-head muted">NOBIS VIDENTUR</div><p class="body-text">Short note about this share of the total goes here, in a few words.</p></div>
      <div class="folio">Page 5</div>
    </div>
  </section>

  <!-- 7 table -->
  <section class="cell">
    <div class="page-label">Page 7</div>
    <div class="slide">
      <div class="sidebar"><div class="brand"><span class="brand-dot"></span><div class="brand-name">Bold Ledger</div></div><div class="site">boldledger.com</div></div>
      <h1 class="title">Title of the page</h1>
      <div class="title-rule"></div>
      <table class="data-table">
        <thead><tr><th style="width:140px"></th><th>A</th><th>B</th><th>C</th></tr></thead>
        <tbody>
          <tr class="band"><td class="row-name">Type 1</td><td>20</td><td>30</td><td>40</td></tr>
          <tr class="gap"><td colspan="4"></td></tr>
          <tr><td class="row-name">Type 2</td><td>50</td><td>60</td><td>70</td></tr>
          <tr class="gap"><td colspan="4"></td></tr>
          <tr class="band"><td class="row-name">Type 3</td><td>80</td><td>90</td><td>100</td></tr>
        </tbody>
      </table>
      <div class="folio">Page 6</div>
    </div>
  </section>

  <!-- 8 team -->
  <section class="cell">
    <div class="page-label">Page 8</div>
    <div class="slide">
      <div class="sidebar"><div class="brand"><span class="brand-dot"></span><div class="brand-name">Bold Ledger</div></div><div class="site">boldledger.com</div></div>
      <h1 class="title">Title of the page</h1>
      <div class="title-rule"></div>
      <div class="member" style="left:104px;top:99px"><div class="member-photo" role="img" aria-label="Portrait photo of Mr A. Smith"></div><div class="member-info"><div class="member-name">Mr A. Smith</div><div class="member-role">(President)</div><p class="body-text">Brief profile of this leader, their role, focus areas and the experience they bring to the team. Add past posts, key results and one line on what drives their work every day.</p></div></div>
      <div class="member" style="left:291px;top:99px"><div class="member-photo" role="img" aria-label="Portrait photo of Mr C. Smith"></div><div class="member-info"><div class="member-name">Mr C. Smith</div><div class="member-role">(President)</div><p class="body-text">Brief profile of this leader, their role, focus areas and the experience they bring to the team. Add past posts, key results and one line on what drives their work every day.</p></div></div>
      <div class="member" style="left:104px;top:221px"><div class="member-photo" role="img" aria-label="Portrait photo of Mr B. Smith"></div><div class="member-info"><div class="member-name">Mr B. Smith</div><div class="member-role">(President)</div><p class="body-text">Brief profile of this leader, their role, focus areas and the experience they bring to the team. Add past posts, key results and one line on what drives their work every day.</p></div></div>
      <div class="member" style="left:291px;top:221px"><div class="member-photo" role="img" aria-label="Portrait photo of Mr D. Smith"></div><div class="member-info"><div class="member-name">Mr D. Smith</div><div class="member-role">(President)</div><p class="body-text">Brief profile of this leader, their role, focus areas and the experience they bring to the team. Add past posts, key results and one line on what drives their work every day.</p></div></div>
      <div class="folio">Page 7</div>
    </div>
  </section>

  <!-- 9 stats -->
  <section class="cell">
    <div class="page-label">Page 9</div>
    <div class="slide">
      <div class="sidebar"><div class="brand"><span class="brand-dot"></span><div class="brand-name">Bold Ledger</div></div><div class="site">boldledger.com</div></div>
      <h1 class="title">Title of the page</h1>
      <div class="title-rule"></div>
      <div class="stat orange" style="left:101px;top:110px">
        <svg width="34" height="30" viewBox="0 0 34 30" fill="none" stroke="var(--white)" stroke-width="2" stroke-linejoin="round"><path d="M3 11 H10 L24 3 V27 L10 19 H3 Z"/><path d="M8 19 L11 28 H15 L13 19"/><path d="M28 10 L32 8 M28 15 H33 M28 20 L32 22"/></svg>
        <div class="stat-figure">915,456,459</div><p class="stat-note">Short line describing this figure and where it comes from.</p>
      </div>
      <div class="stat grey" style="left:288px;top:110px">
        <svg width="34" height="30" viewBox="0 0 34 30" fill="var(--white)"><path d="M13 2 H21 L19 7 H15 Z"/><path d="M15 8 H19 Q30 14 28 24 Q27 29 17 29 Q7 29 6 24 Q4 14 15 8 Z"/><text x="17" y="24" font-family="Lato, sans-serif" font-size="11" font-weight="700" text-anchor="middle" fill="var(--mid-grey)">$</text></svg>
        <div class="stat-figure">111,458,564</div><p class="stat-note">Short line describing this figure and where it comes from.</p>
      </div>
      <div class="stat navy" style="left:101px;top:205px">
        <svg width="34" height="30" viewBox="0 0 34 30" fill="var(--white)"><ellipse cx="17" cy="17" rx="13" ry="9"/><rect x="9" y="23" width="4" height="6"/><rect x="21" y="23" width="4" height="6"/><circle cx="14" cy="5" r="4"/><path d="M29 15 L33 13 V19 L29 18 Z"/></svg>
        <div class="stat-figure">100%</div><p class="stat-note">Short line describing this figure and where it comes from.</p>
      </div>
      <div class="stat ink" style="left:288px;top:205px">
        <svg width="34" height="30" viewBox="0 0 34 30" fill="none" stroke="var(--white)" stroke-width="2"><rect x="4" y="20" width="5" height="8"/><rect x="12" y="14" width="5" height="14"/><rect x="20" y="8" width="5" height="20"/><rect x="28" y="2" width="4" height="26"/></svg>
        <div class="stat-figure">100%</div><p class="stat-note">Short line describing this figure and where it comes from.</p>
      </div>
      <div class="folio">Page 8</div>
    </div>
  </section>

  <!-- 10 closing -->
  <section class="cell">
    <div class="page-label">Page 10</div>
    <div class="slide">
      <div class="closing-band"></div>
      <div class="closing-brand"><span class="brand-dot"></span><div class="brand-name">Bold Ledger</div></div>
      <div class="thanks">THANK YOU</div>
      <div class="closing-site">www.boldledger.com</div>
    </div>
  </section>

</main>
</body>
</html>
```